Quote Cards With KB May 2025 for Instagram

I would like to put these quotes over one of the pictures attached; Instagram (new size: 4:5 (1080 x 1350 pixels) One Quote per picture, and I want the quote to be bold or easy to read as well. I provided a few reference graphics that I really like as examples below. In very small letters at the bottom add @KBHarlowOnline

All of the pictures are attached; you can pick any photo and add one quote to it; but no stock photography

```html
<!DOCTYPE html>
<html lang="en">
<head>
<meta charset="utf-8">
<title>Quote Cards with KB, May 2025</title>
<link href="https://fonts.googleapis.com/css2?family=League+Gothic&family=Roboto+Condensed:wght@400;600;700&family=Poppins:wght@600&display=swap" rel="stylesheet">
<style>
  :root {
    --page: #f2f2f2;
    --magenta-deep: #b0166f;
    --magenta: #c92483;
    --magenta-light: #dc4a9c;
    --tag-bar: #e4488f;
    --ink: #ffffff;
  }
  * { margin: 0; padding: 0; box-sizing: border-box; }
  html, body { width: 1200px; height: 3217px; overflow: hidden; background: var(--page); }
  .sheet { position: relative; width: 1200px; height: 3217px; }

  .card {
    position: absolute;
    width: 461px;
    height: 576px;
    display: grid;
    grid-template-rows: 576px;
    overflow: hidden;
  }
  .card--text-left { grid-template-columns: 54% 46%; }
  .card--photo-left { grid-template-columns: 46% 54%; }
  .col-l { left: 120px; }
  .col-r { left: 620px; }
  .row-1 { top: 81px; }
  .row-2 { top: 693px; }
  .row-3 { top: 1307px; }
  .row-4 { top: 1929px; }
  .row-5 { top: 2560px; }

  .panel {
    background: linear-gradient(160deg, var(--magenta-light) 0%, var(--magenta) 45%, var(--magenta-deep) 100%);
    color: var(--ink);
    padding: 34px 10px 30px 18px;
    display: flex;
    flex-direction: column;
    overflow: hidden;
    min-height: 0;
  }
  .photo { position: relative; }
  .photo--warm { background: linear-gradient(180deg, #6d3a5e 0%, #2c1c2a 100%); }
  .photo--court { background: linear-gradient(180deg, #3a3340 0%, #a17a4a 70%, #d19a2e 100%); }
  .photo--sky { background: linear-gradient(180deg, #a9cbe6 0%, #5c6b4a 60%, #2a2a2a 100%); }
  .photo--night { background: linear-gradient(180deg, #2a2f44 0%, #191b24 100%); }
  .photo--room { background: linear-gradient(180deg, #d9d6d2 0%, #8d8782 55%, #2a2626 100%); }
  .photo--garden { background: linear-gradient(180deg, #b8a2a6 0%, #b77e8e 50%, #c79a2c 100%); }
  .photo--arena { background: linear-gradient(180deg, #2b3f7a 0%, #6a5a68 50%, #2b2a2e 100%); }
  .photo--studio { background: linear-gradient(180deg, #9a9a9c 0%, #3a3a3c 60%, #151515 100%); }

  .handle {
    position: absolute;
    left: 0; right: 0; bottom: 22px;
    height: 20px;
    background: var(--tag-bar);
    color: var(--ink);
    font: 600 13px/20px "Poppins", sans-serif;
    text-align: center;
  }

  .headline {
    font-family: "League Gothic", sans-serif;
    font-weight: 400;
    font-size: 60px;
    line-height: 1.04;
    white-space: nowrap;
  }
  .sub {
    font-family: "Roboto Condensed", sans-serif;
    font-weight: 600;
    font-size: 33px;
    line-height: 1.36;
    margin-top: 24px;
    white-space: nowrap;
  }
  .light { font-weight: 400; }
  .keyword {
    font-family: "Roboto Condensed", sans-serif;
    font-weight: 700;
    font-size: 42px;
    line-height: 1.15;
    white-space: nowrap;
  }
  .cta {
    font-family: "Poppins", sans-serif;
    font-weight: 600;
    font-size: 26px;
    margin-top: auto;
    white-space: nowrap;
  }
</style>
</head>
<body>
<main class="sheet">

  <!-- Row 1 -->
  <article class="card card--text-left col-l row-1">
    <div class="panel">
      <h2 class="headline" style="font-size:66px;line-height:1">Tired.<br>Moody.<br>Stubborn<br>Belly Fat.</h2>
      <p class="sub" style="margin-top:28px">Your hormones<br>are screaming<br>for help!</p>
      <p class="cta">Let’s fix that.</p>
    </div>
    <div class="photo photo--warm" role="img" aria-label="KB posing in a pink gown on a stage">
      <span class="handle">@KBHarlowOnline</span>
    </div>
  </article>

  <article class="card card--text-left col-r row-1">
    <div class="panel">
      <h2 class="headline" style="font-size:60px">That stubborn<br>weight?<br>It’s not your<br>fault</h2>
      <p class="sub" style="font-size:32px;margin-top:22px">Your hormones<br>are to blame<br>and you’re not<br>alone;</p>
      <p class="cta" style="font-size:21px;padding-left:4px">But there is a fix.</p>
    </div>
    <div class="photo photo--court" role="img" aria-label="KB standing courtside on a basketball court">
      <span class="handle">@KBHarlowOnline</span>
    </div>
  </article>

  <!-- Row 2 -->
  <article class="card card--photo-left col-l row-2">
    <div class="photo photo--sky" role="img" aria-label="KB in black outfit on a hillside">
      <span class="handle">@KBHarlowOnline</span>
    </div>
    <div class="panel" style="padding-top:30px">
      <h2 class="headline" style="font-size:64px;line-height:1.08">Your belly<br>isn’t fat…<br><span style="font-size:50px">it’s hormonal.</span></h2>
      <p class="sub" style="font-size:34px;margin-top:34px;line-height:1.4">And here’s<br>how to fix it.<br><span class="light">Comment</span></p>
      <p class="keyword" style="font-size:40px">HORMONES</p>
      <p class="sub light" style="font-size:34px;margin-top:0;line-height:1.4">if nothing is<br>working.</p>
    </div>
  </article>

  <article class="card card--photo-left col-r row-2">
    <div class="photo photo--night" role="img" aria-label="KB in sheer black top by a city window at night">
      <span class="handle">@KBHarlowOnline</span>
    </div>
    <div class="panel" style="padding-top:30px;padding-left:14px">
      <h2 class="headline" style="font-size:52px;line-height:1.1">The stubborn<br><span style="font-size:82px;line-height:1">belly fat</span><br>after 40?</h2>
      <p class="sub" style="margin-top:50px;line-height:1.36">It’s not about<br>calories;<br>it’s about your<br>hormones.</p>
      <p class="cta" style="font-size:24px">Here is the fix!</p>
    </div>
  </article>

  <!-- Row 3 -->
  <article class="card card--text-left col-l row-3">
    <div class="panel">
      <h2 class="headline" style="font-size:62px;line-height:1">Flat tummy<br>in your 40s?</h2>
      <p class="sub" style="font-size:29px;margin-top:42px;line-height:1.4;margin-left:-3px">It’s still possible!<br>Comment</p>
      <p class="keyword" style="font-size:44px;margin-top:4px">BYE BELLY</p>
      <p class="sub" style="font-size:30px;margin-top:0;line-height:1.38">to get the 10<br>secrets to a<br>flatter tummy</p>
    </div>
    <div class="photo photo--room" role="img" aria-label="KB in striped sheer top blowing a kiss">
      <span class="handle">@KBHarlowOnline</span>
    </div>
  </article>

  <article class="card card--text-left col-r row-3">
    <div class="panel">
      <h2 class="headline" style="font-size:62px;line-height:1">Bloating.<br>Muffin top.<br><span style="font-size:52px">Puffy waistline.</span></h2>
      <p class="sub" style="font-size:35px;margin-top:36px;line-height:1.36;margin-left:-3px">Your body’s<br>screaming for<br>a different<br>kind of fix</p>
      <p class="cta">Here it is</p>
    </div>
    <div class="photo photo--room" role="img" aria-label="KB in white crop sweater pointing upward">
      <span class="handle">@KBHarlowOnline</span>
    </div>
  </article>

  <!-- Row 4 -->
  <article class="card card--photo-left col-l row-4">
    <div class="photo photo--garden" role="img" aria-label="KB in pink knit dress among sunflowers">
      <span class="handle">@KBHarlowOnline</span>
    </div>
    <div class="panel" style="padding-top:30px">
      <h2 class="headline" style="font-size:50px;line-height:1.02">You’re doing<br>all the “right”<br>things, but your<br>belly won’t go<br>down?</h2>
      <p class="sub" style="font-size:38px;margin-top:44px;line-height:1.38">Here’s what<br>you haven’t<br>tried.</p>
    </div>
  </article>

  <article class="card card--photo-left col-r row-4">
    <div class="photo photo--arena" role="img" aria-label="KB seated courtside holding a basketball">
      <span class="handle">@KBHarlowOnline</span>
    </div>
    <div class="panel" style="padding-top:34px;padding-left:18px">
      <h2 class="headline" style="font-size:48px;line-height:1.06">This 90-day plan<br>helped women<br><span style="font-size:40px">over 40 slim down,</span></h2>
      <p class="sub" style="font-size:38px;margin-top:40px;line-height:1.4;padding-left:4px">Get a tiny<br>waist and<br>feel sexy<br>again.</p>
      <p class="cta" style="font-size:25px">You’re next.</p>
    </div>
  </article>

  <!-- Row 5 -->
  <article class="card card--text-left col-l row-5">
    <div class="panel" style="padding-top:30px">
      <h2 class="headline" style="font-size:43px;line-height:1.04">This is the secret<br>women over 40<br>are using to get<br>snatched; without<br>starving.</h2>
      <p class="sub" style="font-size:33px;margin-top:52px;padding-left:4px">Comment</p>
      <p class="keyword" style="font-size:52px;margin-top:6px;padding-left:4px">SKINNY</p>
      <p class="sub" style="font-size:33px;margin-top:0;line-height:1.38;padding-left:4px">to get the<br>exact plan.</p>
    </div>
    <div class="photo photo--sky" role="img" aria-label="KB smiling in black outfit outdoors">
      <span class="handle">@KBHarlowOnline</span>
    </div>
  </article>

  <article class="card card--text-left col-r row-5">
    <div class="panel" style="padding-top:30px">
      <h2 class="headline" style="font-size:54px;line-height:1.02">What worked<br>in your 30s<br>won’t work<br>now.</h2>
      <p class="sub" style="font-size:33px;margin-top:58px;line-height:1.36;margin-left:-2px">Here’s what<br>actually does.<br>Drop 30 Pounds<br>in 3 Months.</p>
    </div>
    <div class="photo photo--studio" role="img" aria-label="KB in open-back black top looking over her shoulder">
      <span class="handle">@KBHarlowOnline</span>
    </div>
  </article>

</main>
</body>
</html>
```